Lumra Learning Web Design Project

Who We are:
Lumra Learning is education information portal/ magazine, providing information about the Chinese and International education markets. Our aim is to help school principals improve there curriculum, and parents in understanding this curriculum.

Project Brief:
The site will include education news updates, educational services, curriculum developments and overseas study. We hope the site represents the cross cultural bridge between the west and east. The site will cover both the Sciences and Arts.

Note:
The logo design competition is also underway so we only need the website design

What We want:
This competition is for Design only no coding!
Design a home page based on Template 1,2 or 3. I only need to select one.
The design of an article page.

Optional
Design a Parvex Shutters metro style splash page.

Sites We like:
http://www.qv.com.cn/tonguebridge/default.aspx
http://www.dailyuniversitybulletin.co.uk/
http://kptz.sinocraftlearn.net/

Template Explanations:
Template 1-
The main information has a dynamic sliding category view that when clicked displays the relevant info.
In addition to the main upper menu it also has a left hand sliding menu that pops out on click or gesture

Template 2-
Has limited number of Articles most of the menus are drop downs from the top menu

Template 3-
No Top menu

Target Market(s)

Teachers, principals and parents

Industry/Entity Type

Education

Requirements
Should not have
• kindergarten preschool feel

```html
<!DOCTYPE html>
<html lang="en">
<head>
<meta charset="utf-8">
<title>Lumra Learning – Home</title>
<link href="https://fonts.googleapis.com/css2?family=Arimo:wght@400;700&display=swap" rel="stylesheet">
<style>
:root{
  --red:#d2322d;
  --red-dark:#b8261f;
  --navy:#1f5b8f;
  --navy-dark:#184b78;
  --link:#1a64a6;
  --text:#444;
  --muted:#666;
  --line:#dcdcdc;
  --panel:#f6f6f6;
  --page:#ffffff;
  --band:#f3f3f3;
  --fb:#3b5998;
  --footer-dark:#2a2a2a;
}
*{box-sizing:border-box;margin:0;padding:0}
html,body{width:920px;height:1200px;overflow:hidden}
body{font-family:"Arimo",Arial,sans-serif;background:var(--page);color:var(--text);position:relative;font-size:10px}
.abs{position:absolute}
.header-band{left:0;top:0;width:920px;height:155px;background:var(--band);border-bottom:1px solid #e2e2e2}
.brand{left:68px;top:48px;display:flex;align-items:center;gap:8px}
.brand-dot{width:26px;height:26px;border-radius:50%;background:var(--navy)}
.brand-name{font-size:20px;font-weight:700;color:var(--red);letter-spacing:.2px}
.call{left:626px;top:57px;font-size:14px;color:var(--navy)}
.call span{color:var(--red);margin-left:4px}
.search{left:625px;top:84px;width:153px;height:22px;border:1px solid #ccc;background:#fff;font-size:8.5px;color:#777;padding:6px 10px}
.search svg{position:absolute;right:6px;top:4px}
.lang{left:786px;top:84px;width:65px;height:22px;border:1px solid #ccc;background:#fff;font-size:8.5px;color:#333;padding:5px 0 0 24px}
.lang i{position:absolute;left:7px;top:7px;width:12px;height:8px;background:#2b4a8b}
.lang svg{position:absolute;right:8px;top:8px}
.nav{left:69px;top:134px;width:782px;height:40px;background:linear-gradient(#2e6ea6,var(--navy-dark));border:1px solid #174a76;display:flex}
.nav a{color:#fff;font-weight:700;font-size:11.5px;text-decoration:none;display:flex;align-items:center;justify-content:center;border-right:1px solid #3f7cb2}
.nav a.active{background:linear-gradient(#e8544b,var(--red-dark))}
.hero{left:69px;top:181px;width:782px;height:264px;background:var(--panel);border:1px solid #e0e0e0}
.hero-stage{left:7px;top:6px;width:768px;height:251px;background:linear-gradient(90deg,#c9dbe3,#dde8ed 45%,#d5e4ea)}
.hero-photo{left:0;top:0;width:300px;height:251px;background:linear-gradient(90deg,#6a5446,#c8a48b 55%,#d4e1e7)}
.hero-title{left:239px;top:58px;font-size:19px;font-weight:700;color:#3a3a3a;line-height:26px}
.hero-next{left:539px;top:109px}
.articles{left:491px;top:19px;width:255px;height:213px;background:#fff;border:1px solid #e3e3e3;box-shadow:0 1px 3px rgba(0,0,0,.1)}
.articles h2{font-size:16px;color:var(--red);padding:13px 17px 10px;border-bottom:1px solid #e8e8e8;font-weight:700}
.articles h2 svg{position:absolute;right:14px;top:18px}
.articles h3{font-size:11.5px;color:var(--link);font-weight:400;margin:13px 17px 0}
.articles p{font-size:10px;line-height:16px;color:#555;margin:12px 17px 0;text-align:justify}
.articles .date{font-size:10px;color:#222;margin-top:10px}
.share{display:flex;gap:6px;margin:10px 17px 0;font-size:7.5px}
.share b{border:1px solid #c4cde0;background:#eef2f8;color:#3b5998;padding:2px 4px;border-radius:2px}
.share em{font-style:normal;border:1px solid #ccc;padding:2px 4px;border-radius:2px;color:#333}
.side{left:69px;top:456px;width:130px;height:380px;border:1px solid var(--line);background:#fff}
.side li{list-style:none;height:30.4px;border-bottom:1px solid #e6e6e6;font-size:10.5px;font-weight:700;color:#555;display:flex;align-items:center;padding-left:27px;position:relative;background:#fafafa}
.side li:last-child{border-bottom:0}
.side li:before{content:"››";position:absolute;left:11px;color:#888;font-weight:400}
.cats{left:213px;top:456px;width:442px;height:220px;border:1px solid var(--line);background:#fff}
.acc-head{height:36px;background:linear-gradient(#fafafa,#efefef);border-bottom:1px solid var(--line);font-size:14px;font-weight:700;color:var(--red);padding:10px 16px;position:relative}
.acc-head svg{position:absolute;right:16px;top:15px}
.cat-grid{display:grid;grid-template-columns:149px 148px 140px;padding:11px 0 0 18px;row-gap:0}
.cat-grid span{height:24px;font-size:9.5px;color:#444;display:flex;align-items:center}
.cat-grid span:before{content:"»";margin-right:7px;color:#555}
.acc{left:213px;width:442px;height:36px;border:1px solid var(--line)}
.acc .acc-head{border-bottom:0;height:34px}
.news-title{left:672px;top:459px;font-size:16px;color:var(--red);display:flex;align-items:center;gap:10px}
.news-title i{width:20px;height:16px;background:linear-gradient(#ccd4dc,#9aa6b2);display:block}
.news{left:667px;top:488px;width:184px;height:348px;border:1px solid #e6e6e6;background:#fff;box-shadow:inset 0 0 12px rgba(0,0,0,.06)}
.news-item{position:absolute;left:32px;width:140px}
.news-item:before{content:"";position:absolute;left:-14px;top:5px;border-left:4px solid var(--link);border-top:3px solid transparent;border-bottom:3px solid transparent}
.news-item h4{font-size:10.5px;color:var(--link);font-weight:400}
.news-item p{font-size:8.8px;color:#777;line-height:13px;margin-top:5px}
.news-item time{display:block;font-size:8px;color:#222;margin-top:5px}
.fb-band{left:68px;top:846px;width:784px;height:106px;background:var(--fb);border-radius:2px}
.fb-name{left:44px;top:22px;font-size:28px;font-weight:700;color:#fff}
.fb-like{left:74px;top:66px;display:flex;gap:4px;font-size:7.5px}
.fb-like b{background:#eef2f8;color:#3b5998;padding:2px 5px;border-radius:2px}
.fb-like em{font-style:normal;background:#fff;padding:2px 4px;color:#333;border-radius:2px}
.fb-box{left:209px;top:18px;width:535px;height:73px;background:#fff;border-radius:3px}
.fb-box .cap{position:absolute;left:5px;top:4px;font-size:7.5px;color:#333}
.fb-box .cap u{text-decoration:none;color:#3b5998}
.faces{position:absolute;left:6px;top:17px;display:flex;gap:4.6px}
.face{width:40px;text-align:center;font-size:6.5px;color:#777}
.face div{width:40px;height:40px;margin-bottom:3px}
.footer{left:0;top:963px;width:920px;height:187px;background:#f5f5f5;border-top:2px solid #e2e2e2}
.foot-h{font-size:13px;color:#333}
.ql{top:1016px;list-style:none}
.ql li{font-size:9.5px;color:#777;height:22.4px}
.ql li:before{content:"•";margin-right:5px;color:#999}
.divider{left:665px;top:978px;width:1px;height:157px;background:#ccc}
.social{left:693px;display:flex;align-items:center;font-size:9.5px;color:#777}
.social i{width:21px;height:21px;margin-right:17px;border-radius:2px;display:block}
.social b{font-weight:400;font-size:11px;margin-left:5px}
.bottom{left:0;top:1150px;width:920px;height:50px;background:var(--footer-dark);color:#aaa;font-size:10px;text-align:center;padding-top:21px}
</style>
</head>
<body>
<div class="abs header-band"></div>
<div class="abs brand"><span class="brand-dot"></span><span class="brand-name">LUMRA LEARNING</span></div>
<div class="abs call">Call us : <span>555 014 2290</span></div>
<div class="abs search">Search<svg width="13" height="13" viewBox="0 0 13 13"><circle cx="5" cy="5" r="3.8" fill="none" stroke="#333" stroke-width="1.8"/><path d="M8 8l4 4" stroke="#333" stroke-width="2"/></svg></div>
<div class="abs lang"><i></i>Eng<svg width="7" height="5"><path d="M0 0h7L3.5 5z" fill="#333"/></svg></div>
<nav class="abs nav">
  <a class="active" style="width:77px">Home</a><a style="width:76px">About</a><a style="width:81px">Service</a><a style="width:70px">News</a><a style="width:86px">Features</a><a style="width:81px">Awards</a><a style="width:80px">Schools</a><a style="width:80px">Career</a><a style="width:84px">Support</a><a style="width:65px;border:0">FAQ</a>
</nav>

<section class="abs hero">
  <div class="abs hero-stage">
    <div class="abs hero-photo" role="img" aria-label="Photo of a smiling student holding a folder"></div>
    <div class="abs hero-title">Suspendisse leo lectus,<br>blandit in pretium</div>
    <svg class="abs hero-next" width="32" height="32"><circle cx="16" cy="16" r="15.5" fill="#fff" stroke="#ddd"/><path d="M14 10l6 6-6 6" fill="none" stroke="#999" stroke-width="1.6"/></svg>
    <div class="abs articles">
      <h2>Latest Articles<svg width="10" height="9"><path d="M0 0l5 4.5L0 9zM5 0l5 4.5L5 9z" fill="#aaa"/></svg></h2>
      <h3>Maecenas bibendum consectetur</h3>
      <p>Proin consequat tellus eu nulla tempus mollis. Donec consequat elit vel malesuada sollicitudin. Donec non metus sed lorem fermentum condi mentum. In hac habitasse platea dictumst. Sed molestie a augue commodo adipiscing.</p>
      <p class="date">July-16-2013</p>
      <div class="share"><b>Like</b><em>3k</em><b>Share</b><em>316</em></div>
    </div>
  </div>
</section>

<ul class="abs side">
  <li>Side bar Menu 1</li><li>Side bar Menu 2</li><li>Side bar Menu 3</li><li>Side bar Menu 4</li><li>Side bar Menu 5</li><li>Side bar Menu 6</li><li>Side bar Menu 7</li><li>Side bar Menu 8</li><li>Side bar Menu 9</li><li>Side bar Menu 10</li><li>Side bar Menu 11</li><li>Side bar Menu 12</li>
</ul>

<section class="abs cats">
  <div class="acc-head">Categories<svg width="10" height="6"><path d="M1 5l4-4 4 4" fill="none" stroke="#888" stroke-width="1.6"/></svg></div>
  <div class="cat-grid">
    <span>Sed ultricies</span><span>Sed ultricies</span><span>Sed ultricies</span>
    <span>Maecenas massa diam</span><span>Maecenas massa diam</span><span>Maecenas massa diam</span>
    <span>Etiam gravida</span><span>Etiam gravida</span><span>Etiam gravida</span>
    <span>Fusce hendrerit erat</span><span>Fusce hendrerit erat</span><span>Fusce hendrerit erat</span>
    <span>Proin id tellus</span><span>Proin id tellus</span><span>Proin id tellus</span>
    <span>Nulla in neque</span><span>Nulla in neque</span><span>Nulla in neque</span>
    <span>Praesent acauctor</span><span>Praesent acauctor</span><span>Praesent acauctor</span>
  </div>
</section>
<div class="abs acc" style="top:680px"><div class="acc-head">Europe<svg width="10" height="6"><path d="M1 1l4 4 4-4" fill="none" stroke="#888" stroke-width="1.6"/></svg></div></div>
<div class="abs acc" style="top:720px"><div class="acc-head">Drama<svg width="10" height="6"><path d="M1 1l4 4 4-4" fill="none" stroke="#888" stroke-width="1.6"/></svg></div></div>
<div class="abs acc" style="top:760px"><div class="acc-head">Asia<svg width="10" height="6"><path d="M1 1l4 4 4-4" fill="none" stroke="#888" stroke-width="1.6"/></svg></div></div>
<div class="abs acc" style="top:800px"><div class="acc-head">Science<svg width="10" height="6"><path d="M1 1l4 4 4-4" fill="none" stroke="#888" stroke-width="1.6"/></svg></div></div>

<div class="abs news-title"><i></i>Latest News</div>
<aside class="abs news">
  <div class="news-item" style="top:22px"><h4>Frozen Door</h4><p>Nulla facilisi. Curabitur at elit , eget hen drerit felis vehicula.</p><time>July-11-2013</time></div>
  <div class="news-item" style="top:103px"><h4>Frozen Door</h4><p>Nulla facilisi. Curabitur at elit , eget hen drerit felis vehicula.</p><time>July-11-2013</time></div>
  <div class="news-item" style="top:183px"><h4>Frozen Door</h4><p>Nulla facilisi. Curabitur at elit , eget hen drerit felis vehicula.</p><time>July-11-2013</time></div>
  <div class="news-item" style="top:264px"><h4>Frozen Door</h4><p>Nulla facilisi. Curabitur at elit , eget hen drerit felis vehicula.</p><time>July-11-2013</time></div>
</aside>

<section class="abs fb-band">
  <div class="abs fb-name">friendhub</div>
  <div class="abs fb-like"><b>Like</b><em>3k</em></div>
  <div class="abs fb-box">
    <div class="cap">64 people like <u>Reading Porch</u></div>
    <div class="faces">
      <div class="face"><div role="img" aria-label="Member photo" style="background:#9a9a9a"></div>Tavin</div>
      <div class="face"><div role="img" aria-label="Member photo" style="background:#7a6a5e"></div>Rolan</div>
      <div class="face"><div role="img" aria-label="Member photo" style="background:#8a6a4e"></div>Corrie</div>
      <div class="face"><div role="img" aria-label="Member photo" style="background:#cfc7c0"></div>Maribel</div>
      <div class="face"><div role="img" aria-label="Member photo" style="background:#a07a4a"></div>Velin</div>
      <div class="face"><div role="img" aria-label="Member photo" style="background:#6e5a50"></div>Sarodu</div>
      <div class="face"><div role="img" aria-label="Member photo" style="background:#7d5a42"></div>Orin</div>
      <div class="face"><div role="img" aria-label="Member photo" style="background:#5a4a44"></div>Lorena</div>
      <div class="face"><div role="img" aria-label="Member photo" style="background:#8a5a40"></div>Kavya</div>
      <div class="face"><div role="img" aria-label="Member photo" style="background:#b8aa98"></div>Selma</div>
      <div class="face"><div role="img" aria-label="Member photo" style="background:#4a4e66"></div>Darin</div>
      <div class="face"><div role="img" aria-label="Member photo" style="background:#3a3a3a"></div>IVA</div>
    </div>
  </div>
</section>

<footer class="abs footer"></footer>
<div class="abs foot-h" style="left:70px;top:980px">Quick Links</div>
<ul class="abs ql" style="left:72px"><li>Integer lobortis</li><li>Curabitur ac</li><li>Phasellus tellus nisl</li><li>Aenean fringilla</li><li>Vestibulum</li><li>Aliquam commodo</li></ul>
<ul class="abs ql" style="left:227px"><li>Integer lobortis</li><li>Curabitur ac</li><li>Phasellus tellus nisl</li><li>Aenean fringilla</li><li>Vestibulum</li><li>Aliquam commodo</li></ul>
<ul class="abs ql" style="left:382px"><li>Integer lobortis</li><li>Curabitur ac</li><li>Phasellus tellus nisl</li><li>Aenean fringilla</li><li>Vestibulum</li><li>Aliquam commodo</li></ul>
<ul class="abs ql" style="left:537px"><li>Integer lobortis</li><li>Curabitur ac</li><li>Phasellus tellus nisl</li><li>Aenean fringilla</li><li>Vestibulum</li><li>Aliquam commodo</li></ul>
<div class="abs divider"></div>
<div class="abs foot-h" style="left:693px;top:980px">Connect with us</div>
<div class="abs social" style="top:1012px"><i style="background:#3b5998"></i>Join with us on<b style="color:#2b4a8b">Friendhub</b></div>
<div class="abs social" style="top:1044px"><i style="background:#2fa8dc"></i>Follow us on<b style="color:#2a9fd6">Chirpline</b></div>
<div class="abs social" style="top:1076px"><i style="background:#1b6ea8"></i>Share on<b style="color:#1b6ea8">Linkwork</b></div>
<div class="abs social" style="top:1108px"><i style="background:#c9302c"></i>Watch on<b style="color:#222">Clipstream</b></div>
<div class="abs bottom">Copyright © 2013 &nbsp;Lumra Learning &nbsp; All rights reserved.</div>
</body>
</html>
```